National online rug retailer needs a home page design

See the FloorNest logo and create a home page design around that color theme. Details are spelled out in word document uploaded below.

Apparently this website did not take my attachement showing the logo and basic requirements.  If you would send me your email address, I will send you the attachment directly.
Best regards,
Tom Vance
tvance@mrdcorp.example

Target Market(s)

The target market is home owners 25 to 75 years old with combined incomes over $100,000 per year.

Industry/Entity Type

Online

Requirements
Must have
• Lots of white space with black letters and creative use of red and possibly one other color. Would like a compelling call to action button.

```html
<!DOCTYPE html>
<html lang="en">
<head>
<meta charset="utf-8">
<title>FloorNest.com – Home</title>
<link href="https://fonts.googleapis.com/css2?family=Mulish:wght@400;600;700&family=Arimo:wght@400;700&display=swap" rel="stylesheet">
<style>
:root{
  --red:#e00000;
  --red-dark:#b80000;
  --ink:#222;
  --muted:#666;
  --line:#e2e2e2;
  --nav:#4b4b4b;
  --foot:#f0f0f0;
  --white:#fff;
}
*{box-sizing:border-box;margin:0;padding:0}
html,body{width:815px;height:1200px;overflow:hidden;background:var(--white)}
body{position:relative;font-family:"Mulish",sans-serif;color:var(--ink);font-size:8px}
.abs{position:absolute}
a{color:inherit;text-decoration:none}

/* header */
.brand{left:90px;top:18px;height:50px}
.brand-name{font-size:32px;font-weight:600;color:var(--red);line-height:36px;display:flex;align-items:center;gap:8px}
.brand-name .mark{width:14px;height:14px;background:var(--red)}
.brand-tag{font-size:7.5px;color:var(--muted);margin-left:62px;margin-top:2px}
.search{left:332px;top:33px;width:151px;height:24px;border:1px solid #ccc;font-size:7px;color:#888;padding:7px 8px}
.search-btn{left:485px;top:33px;width:24px;height:24px;background:#777;display:flex;align-items:center;justify-content:center}
.account{right:84px;top:19px;text-align:right;font-size:8px;color:var(--muted);line-height:16px}
.account b{color:var(--ink);font-weight:400}
.account .phone{font-size:11px}
.account .phone b{font-size:11.5px}
.account .red{color:var(--red)}
.nav{left:82px;top:94px;width:652px;height:30px;background:var(--nav);border-bottom:3px solid var(--red);border-radius:2px;display:flex;align-items:center;justify-content:space-around;color:var(--white);font-size:9.5px}
.nav .sep{color:#aaa}

/* sidebar */
.browse{left:82px;top:138px;width:154px;height:252px;border:1px solid var(--line);border-radius:3px;overflow:hidden}
.browse h2{background:var(--red);color:var(--white);font-size:12px;font-weight:400;height:30px;line-height:30px;padding-left:13px;border-bottom:2px solid var(--red-dark)}
.browse li{list-style:none;height:27.7px;border-bottom:1px solid var(--line);display:flex;justify-content:space-between;align-items:center;padding:0 10px 0 13px;font-family:"Arimo",sans-serif;font-size:8px;font-weight:700;color:#333;background:#fbfbfb}
.browse li:last-child{border-bottom:0}

/* hero */
.hero{left:250px;top:138px;width:482px;height:252px;border-radius:3px;overflow:hidden;background:linear-gradient(160deg,#8b7a62 0%,#c9a677 40%,#7fa9a6 65%,#b9c8c4 100%)}
.hero-cap{position:absolute;left:0;bottom:0;width:100%;height:42px;background:rgba(30,30,30,.78);color:var(--white);font-size:17px;padding:10px 15px}
.hero-dots{position:absolute;right:12px;bottom:14px;display:flex;gap:5px}
.hero-dots span{width:13px;height:13px;border-radius:50%;background:var(--white)}

/* promo */
.promo{top:406px;height:78px;background:var(--red);border-radius:3px;overflow:hidden;color:var(--white)}
.promo h3{font-size:16px;font-weight:400;margin:10px 0 0 9px}
.promo p{font-size:7.5px;margin:5px 0 0 9px;width:100px;line-height:11px}
.promo .pic{position:absolute;right:0;top:0;width:95px;height:78px;clip-path:polygon(12% 0,100% 0,100% 100%,0 100%)}
.promo .cta{position:absolute;right:46px;bottom:0;background:#666;font-size:9px;padding:3px 9px 2px;border-radius:3px 0 0 0}

/* sections */
.sec-head{left:82px;width:652px;height:32px;border-top:1px solid var(--line);border-bottom:1px solid var(--line);display:flex;align-items:center;justify-content:space-between;padding:0 12px 0 5px}
.sec-head h2{font-family:"Arimo",sans-serif;font-size:11px;color:var(--red);font-weight:700}
.arrows{display:flex;gap:3px}
.product{width:133px;height:150px}
.product .pic{width:133px;height:98px}
.product .rule{position:absolute;top:107px;left:0;width:133px;border-top:1px solid var(--line)}
.product .rule::before{content:"";position:absolute;left:12px;top:-1px;width:13px;border-top:1px solid var(--red)}
.product .sale{position:absolute;left:110px;top:-4px;width:34px;height:34px;border-radius:50%;background:#555;color:var(--white);font-size:8px;display:flex;align-items:center;justify-content:center}
.product .name{position:absolute;top:124px;left:1px;font-family:"Arimo",sans-serif;font-size:7.5px}
.product .price{position:absolute;top:137px;left:1px;font-family:"Arimo",sans-serif;font-size:10px}
.product .price em{font-style:normal;color:var(--red)}
.product .cart{position:absolute;left:110px;top:125px;width:23px;height:23px;background:var(--red);border-radius:2px;display:flex;align-items:center;justify-content:center}

/* footer */
.footer{left:82px;top:954px;width:652px;height:210px;background:var(--foot)}
.foot-col{position:absolute;top:20px}
.foot-col h4{font-size:9px;font-weight:700;color:#333;margin-bottom:24px}
.foot-col li{list-style:none;font-size:7.5px;color:#444;line-height:13px}
.foot-rule{position:absolute;left:18px;top:42px;width:602px;border-top:1px solid #ddd}
.badges{position:absolute;left:406px;top:58px;width:220px}
.badge{position:absolute;background:#d0d0d0;border-radius:2px}
.copy{left:82px;top:1164px;width:652px;height:36px;background:var(--nav);color:#bbb;font-size:7.5px;text-align:center;line-height:36px}
</style>
</head>
<body>

<header>
  <div class="abs brand">
    <div class="brand-name"><span class="mark"></span>FloorNest.com</div>
    <div class="brand-tag">for domestic and heirloom values</div>
  </div>
  <div class="abs search">Enter a keyword or item</div>
  <div class="abs search-btn">
    <svg width="12" height="12" viewBox="0 0 12 12"><circle cx="5" cy="5" r="3.6" fill="none" stroke="#fff" stroke-width="1.5"/><line x1="7.6" y1="7.6" x2="11" y2="11" stroke="#fff" stroke-width="1.6"/></svg>
  </div>
  <div class="abs account">
    <div>Items (0) <b>Total $0.00</b> View Cart &nbsp;|&nbsp; Checkout</div>
    <div class="phone">Order Toll-Free &nbsp;: &nbsp;<b>1-800-555-0142</b></div>
    <div>My Account &nbsp;|&nbsp; Sign &nbsp;<span class="red">&#9679;</span> Live Chat &nbsp;<span class="red">&#9679;</span> Online</div>
  </div>
  <nav class="abs nav">
    <a>Home</a><span class="sep">|</span><a>Selection guides</a><span class="sep">|</span><a>Rug Care</a><span class="sep">|</span><a>FAQ</a><span class="sep">|</span><a>Return Policy</a><span class="sep">|</span><a>Free Shipping</a><span class="sep">|</span><a>Clearance Rugs</a>
  </nav>
</header>

<aside class="abs browse">
  <h2>Browse</h2>
  <ul>
    <li>RUG THEME<span>+</span></li>
    <li>COLOR WAY<span>+</span></li>
    <li>SIZE<span>+</span></li>
    <li>SHAPE<span>+</span></li>
    <li>FIBER CONTENT<span>+</span></li>
    <li>MFGR. BRAND<span>+</span></li>
    <li>MFGR.COLLECTION<span>+</span></li>
    <li>PRICE<span>+</span></li>
  </ul>
</aside>

<section class="abs hero" role="img" aria-label="Living room with a striped teal rug on a wooden floor beside a fireplace">
  <div class="hero-cap">For Domestic and Heirloom values</div>
  <div class="hero-dots"><span></span><span></span></div>
</section>

<section class="abs promo" style="left:82px;width:214px">
  <h3>Traditional</h3><p>Lorem Ipsum is simply dummy text of the</p>
  <div class="pic" role="img" aria-label="Purple patterned rug" style="background:linear-gradient(135deg,#8a5aa8,#5b2f7a)"></div>
  <div class="cta">Click here.</div>
</section>
<section class="abs promo" style="left:300px;width:214px">
  <h3>Transitional</h3><p>Lorem Ipsum is simply dummy text of the</p>
  <div class="pic" role="img" aria-label="Red floral rug" style="background:linear-gradient(135deg,#a33a2a,#c9974d)"></div>
  <div class="cta">Click here.</div>
</section>
<section class="abs promo" style="left:518px;width:216px">
  <h3>Casual</h3><p>Lorem Ipsum is simply dummy text of the</p>
  <div class="pic" role="img" aria-label="Modern room with a black chair" style="background:linear-gradient(135deg,#d8d8d8,#8f8f8f)"></div>
  <div class="cta">Click here.</div>
</section>

<div class="abs sec-head" style="top:502px"><h2>NEW PRODUCTS</h2>
  <div class="arrows"><svg width="20" height="11" viewBox="0 0 20 11"><path d="M8 0v11L0 5.5z M12 0v11l8-5.5z" fill="#555"/></svg></div>
</div>

<div class="abs product" style="left:89px;top:556px"><div class="pic" role="img" aria-label="Dark rug with colourful circles" style="background:linear-gradient(135deg,#7a4a2a,#2a1a14)"></div><div class="sale">Sale</div><div class="rule"></div><div class="name">Lorem ipsum dolor sit</div><div class="price">$219.00 <em>$182.00</em></div><div class="cart"><svg width="11" height="10" viewBox="0 0 11 10"><path d="M0 1h2l1.5 5h5.5L10.5 2.5H3" fill="none" stroke="#fff" stroke-width="1.3"/><circle cx="4" cy="8.6" r="1" fill="#fff"/><circle cx="8.5" cy="8.6" r="1" fill="#fff"/></svg></div></div>
<div class="abs product" style="left:256px;top:556px"><div class="pic" role="img" aria-label="Bright room with grey striped rug" style="background:linear-gradient(135deg,#e4e4e4,#8e9a9a)"></div><div class="sale">Sale</div><div class="rule"></div><div class="name">Lorem ipsum dolor sit</div><div class="price">$219.00 <em>$182.00</em></div><div class="cart"><svg width="11" height="10" viewBox="0 0 11 10"><path d="M0 1h2l1.5 5h5.5L10.5 2.5H3" fill="none" stroke="#fff" stroke-width="1.3"/><circle cx="4" cy="8.6" r="1" fill="#fff"/><circle cx="8.5" cy="8.6" r="1" fill="#fff"/></svg></div></div>
<div class="abs product" style="left:425px;top:556px"><div class="pic" role="img" aria-label="Sofa with a red and grey swirl rug" style="background:linear-gradient(160deg,#b2403c,#c9c4bd 55%,#777)"></div><div class="sale">Sale</div><div class="rule"></div><div class="name">Lorem ipsum dolor sit</div><div class="price">$219.00 <em>$182.00</em></div><div class="cart"><svg width="11" height="10" viewBox="0 0 11 10"><path d="M0 1h2l1.5 5h5.5L10.5 2.5H3" fill="none" stroke="#fff" stroke-width="1.3"/><circle cx="4" cy="8.6" r="1" fill="#fff"/><circle cx="8.5" cy="8.6" r="1" fill="#fff"/></svg></div></div>
<div class="abs product" style="left:592px;top:556px"><div class="pic" role="img" aria-label="Red rug on a wooden floor" style="background:linear-gradient(160deg,#d9c3a0,#a8191a 55%,#c6a57c)"></div><div class="sale">Sale</div><div class="rule"></div><div class="name">Lorem ipsum dolor sit</div><div class="price">$219.00 <em>$182.00</em></div><div class="cart"><svg width="11" height="10" viewBox="0 0 11 10"><path d="M0 1h2l1.5 5h5.5L10.5 2.5H3" fill="none" stroke="#fff" stroke-width="1.3"/><circle cx="4" cy="8.6" r="1" fill="#fff"/><circle cx="8.5" cy="8.6" r="1" fill="#fff"/></svg></div></div>

<div class="abs sec-head" style="top:726px"><h2>YOU MAY ALSO LIKE</h2>
  <div class="arrows"><svg width="20" height="11" viewBox="0 0 20 11"><path d="M8 0v11L0 5.5z M12 0v11l8-5.5z" fill="#555"/></svg></div>
</div>

<div class="abs product" style="left:89px;top:780px"><div class="pic" role="img" aria-label="White sofa with a cream patterned rug" style="background:linear-gradient(160deg,#6a4a30,#eee8dd 55%,#c79a68)"></div><div class="rule"></div><div class="name">Lorem ipsum dolor sit</div><div class="price">$219.00 <em>$182.00</em></div><div class="cart"><svg width="11" height="10" viewBox="0 0 11 10"><path d="M0 1h2l1.5 5h5.5L10.5 2.5H3" fill="none" stroke="#fff" stroke-width="1.3"/><circle cx="4" cy="8.6" r="1" fill="#fff"/><circle cx="8.5" cy="8.6" r="1" fill="#fff"/></svg></div></div>
<div class="abs product" style="left:256px;top:780px"><div class="pic" role="img" aria-label="Teal striped rug" style="background:linear-gradient(160deg,#b89a6e,#7aa8a6 50%,#c8c8c0)"></div><div class="rule"></div><div class="name">Lorem ipsum dolor sit</div><div class="price">$219.00 <em>$182.00</em></div><div class="cart"><svg width="11" height="10" viewBox="0 0 11 10"><path d="M0 1h2l1.5 5h5.5L10.5 2.5H3" fill="none" stroke="#fff" stroke-width="1.3"/><circle cx="4" cy="8.6" r="1" fill="#fff"/><circle cx="8.5" cy="8.6" r="1" fill="#fff"/></svg></div></div>
<div class="abs product" style="left:425px;top:780px"><div class="pic" role="img" aria-label="Rug with grey, black and green arcs" style="background:linear-gradient(160deg,#d8c29c,#6f6a62 45%,#8fbf3a 70%,#d6bf96)"></div><div class="rule"></div><div class="name">Lorem ipsum dolor sit</div><div class="price">$219.00 <em>$182.00</em></div><div class="cart"><svg width="11" height="10" viewBox="0 0 11 10"><path d="M0 1h2l1.5 5h5.5L10.5 2.5H3" fill="none" stroke="#fff" stroke-width="1.3"/><circle cx="4" cy="8.6" r="1" fill="#fff"/><circle cx="8.5" cy="8.6" r="1" fill="#fff"/></svg></div></div>
<div class="abs product" style="left:592px;top:780px"><div class="pic" role="img" aria-label="Navy and red traditional rug" style="background:linear-gradient(160deg,#d9c6a6,#7a3a2a 40%,#2b2f55 60%,#c6a47a)"></div><div class="rule"></div><div class="name">Lorem ipsum dolor sit</div><div class="price">$219.00 <em>$182.00</em></div><div class="cart"><svg width="11" height="10" viewBox="0 0 11 10"><path d="M0 1h2l1.5 5h5.5L10.5 2.5H3" fill="none" stroke="#fff" stroke-width="1.3"/><circle cx="4" cy="8.6" r="1" fill="#fff"/><circle cx="8.5" cy="8.6" r="1" fill="#fff"/></svg></div></div>

<footer class="abs footer">
  <div class="foot-rule"></div>
  <div class="foot-col" style="left:18px"><h4>Customer Services</h4><ul>
    <li>Shipping</li><li>Return Policy</li><li>Privacy Policy</li><li>Ordering &amp; Delivery</li><li>Checklist</li><li>Terms of Use</li><li>Terms of Sale</li><li>Contact Us</li><li>Environmental Policy</li></ul></div>
  <div class="foot-col" style="left:149px"><h4>Resources</h4><ul>
    <li>Product Articles</li><li>Learning Center</li><li>Help</li><li>Refer A Friend</li><li>FloorNest Blog</li><li>Room Scene Viewer</li><li>Site Map</li><li>FAQ</li><li>Customer Testimonials</li><li>Photo Gallery</li></ul></div>
  <div class="foot-col" style="left:272px"><h4>Corporate Info</h4><ul>
    <li>About FloorNest.com</li><li>Careers</li><li>Affiliates</li></ul></div>
  <div class="foot-col" style="left:406px"><h4>Payments &amp; Security</h4></div>
  <div class="badges">
    <div class="badge" style="left:2px;top:0;width:21px;height:14px"></div>
    <div class="badge" style="left:27px;top:0;width:21px;height:14px"></div>
    <div class="badge" style="left:52px;top:0;width:21px;height:14px"></div>
    <div class="badge" style="left:77px;top:0;width:21px;height:14px"></div>
    <div class="badge" style="left:102px;top:0;width:21px;height:14px"></div>
    <div class="badge" style="left:130px;top:-6px;width:86px;height:26px"></div>
    <div class="badge" style="left:0;top:32px;width:30px;height:30px;border-radius:50%"></div>
    <div class="badge" style="left:38px;top:32px;width:30px;height:30px;border-radius:50%"></div>
    <div class="badge" style="left:74px;top:40px;width:40px;height:16px"></div>
    <div class="badge" style="left:120px;top:38px;width:38px;height:20px"></div>
    <div class="badge" style="left:166px;top:34px;width:50px;height:24px"></div>
  </div>
</footer>
<div class="abs copy">© Copyrights 2013 &nbsp;FloorNest. All rights Reserved</div>

</body>
</html>
```